Marwick Law Letterhead

We need a new letterhead design for a Law Firm. The address for the law firm is 1475 Calloway Street, Suite 210, Houston, Texas 77041. Phone Number: 832-361-9027; Fax Number: 832-614-7359. The logo is uploaded to the project.

```html
<!DOCTYPE html>
<html lang="en">
<head>
<meta charset="utf-8">
<title>Marwick Law Letterhead</title>
<link href="https://fonts.googleapis.com/css2?family=Montserrat:wght@400;500;600;700&display=swap" rel="stylesheet">
<style>
  :root {
    --navy: #1b2c5c;
    --red: #c8161e;
    --red-dark: #8f0d14;
    --ink: #231f20;
    --paper: #ffffff;
    --backdrop: #cfcfcf;
  }
  * { margin: 0; padding: 0; box-sizing: border-box; }
  html, body {
    width: 1200px; height: 1200px; overflow: hidden;
    background: var(--backdrop);
    font-family: "Montserrat", sans-serif;
  }
  .letterhead {
    position: absolute; left: 151px; top: 20px;
    width: 897px; height: 1160px;
    background: var(--paper);
    overflow: hidden;
  }
  .header-frame {
    position: absolute; left: 35px; top: 29px;
    width: 828px; height: 143px;
    border: 3px solid var(--navy);
    border-radius: 24px;
  }
  .brand {
    position: absolute; left: 68px; top: 64px;
    display: flex; align-items: center; gap: 18px;
  }
  .brand-mark {
    width: 66px; height: 66px; background: var(--navy);
  }
  .brand-name {
    font-size: 36px; font-weight: 600; color: var(--navy);
    letter-spacing: 0.5px;
  }
  .contact-band {
    position: absolute; left: 426px; top: 45px;
    width: 471px; height: 106px;
    border-radius: 20px 0 0 20px;
    background: linear-gradient(180deg, var(--red-dark) 0%, var(--red) 70%);
    color: #fff;
  }
  .phone-list { position: absolute; left: 30px; top: 19px; }
  .phone-row {
    display: flex; align-items: center; gap: 14px;
    height: 31px;
    font-size: 20px; font-weight: 600; letter-spacing: 1px;
  }
  .phone-row svg { width: 18px; height: 18px; fill: #fff; }
  .band-divider {
    position: absolute; left: 237px; top: 28px;
    width: 2px; height: 44px; background: #fff;
  }
  .address {
    position: absolute; left: 255px; top: 23px;
    font-size: 14px; font-weight: 600; line-height: 17.5px; letter-spacing: 0.6px;
  }
  .letter-body { position: absolute; left: 71px; top: 230px; color: var(--ink); }
  .recipient-name { font-size: 19px; font-weight: 700; }
  .recipient-detail { font-size: 14px; margin-top: 8px; }
  .paragraph {
    font-size: 17.2px; line-height: 25px; letter-spacing: 0.2px;
    white-space: nowrap;
  }
  .paragraph:first-of-type { margin-top: 30px; }
  .paragraph + .paragraph { margin-top: 23px; }
  .sign-off {
    position: absolute; right: 99px; top: 988px;
    text-align: right; font-size: 19px; font-weight: 700; line-height: 25px;
    color: var(--ink);
  }
  .footer-rule {
    position: absolute; left: 0; top: 1120px;
    width: 100%; height: 3px; background: var(--red);
  }
  .web-pill {
    position: absolute; left: 249px; top: 1099px;
    width: 399px; height: 40px; border-radius: 20px;
    background: var(--navy); color: #fff;
    display: flex; align-items: center; justify-content: center;
    font-size: 26px; font-weight: 500; letter-spacing: 1.5px;
  }
</style>
</head>
<body>
  <div class="letterhead">
    <div class="header-frame"></div>

    <div class="brand">
      <div class="brand-mark"></div>
      <div class="brand-name">Marwick Law</div>
    </div>

    <div class="contact-band">
      <div class="phone-list">
        <div class="phone-row">
          <svg viewBox="0 0 24 24" aria-hidden="true"><path d="M6.6 10.8a15.1 15.1 0 0 0 6.6 6.6l2.2-2.2c.3-.3.7-.4 1-.2 1.1.4 2.3.6 3.6.6.6 0 1 .4 1 1V20c0 .6-.4 1-1 1A17 17 0 0 1 3 4c0-.6.4-1 1-1h3.5c.6 0 1 .4 1 1 0 1.3.2 2.5.6 3.6.1.3 0 .7-.2 1z"/></svg>
          <span>832-361-9027</span>
        </div>
        <div class="phone-row">
          <svg viewBox="0 0 24 24" aria-hidden="true"><path d="M7 2h9l3 3v5h2v12H3V10h4zm2 2v6h8V6h-2V4zM6 13v2h2v-2zm4 0v2h2v-2zm4 0v2h2v-2zm-8 4v2h2v-2zm4 0v2h2v-2zm4 0v2h2v-2z"/></svg>
          <span>832-614-7359</span>
        </div>
      </div>
      <div class="band-divider"></div>
      <div class="address">1475 Calloway<br>Street, Suite 210,<br>Houston, Texas 77041</div>
    </div>

    <main class="letter-body">
      <div class="recipient-name">Lorem Ipsum is simply</div>
      <div class="recipient-detail">Lorem Ipsum is simply</div>

      <p class="paragraph">Lorem Ipsum is simply dummy text of the printing and typesetting industry.<br>Lorem Ipsum has been the industry's standard dummy text ever since the<br>1500s, when an unknown printer took a galley of type and scrambled it to make<br>a type specimen book. It has survived not only five centuries, but also the leap<br>into electronic typesetting, remaining essentially unchanged. It was popularised<br>in the 1960s with the release of Tessarine sheets containing Lorem Ipsum<br>passages, and more recently with desktop publishing software like Corvane<br>PageSetter including versions of Lorem Ipsum.</p>

      <p class="paragraph">Lorem Ipsum is simply dummy text of the printing and typesetting industry.<br>Lorem Ipsum has been the industry's standard dummy text ever since the<br>1500s, when an unknown printer took a galley of type and scrambled it to make<br>a type specimen book. It has survived not only five centuries, but also the leap<br>into electronic typesetting, remaining essentially unchanged. It was popularised<br>in the 1960s with the release of Tessarine sheets containing Lorem Ipsum<br>passages, and more recently with desktop publishing software like Corvane<br>PageSetter including versions of Lorem Ipsum.</p>

      <p class="paragraph">Lorem Ipsum is simply dummy text of the printing and typesetting industry.<br>Lorem Ipsum has been the industry's standard dummy text ever since the<br>1500s, when an unknown printer took a galley of type and scrambled it to make<br>a type specimen book. It has survived not only five centuries, but also the leap<br>into electronic typesetting, remaining essentially unchanged. It was popularised<br>in the 1960s with the release of Tessarine sheets containing Lorem Ipsum<br>passages, and more recently with desktop publishing software like Corvane<br>PageSetter including versions of Lorem Ipsum.</p>
    </main>

    <div class="sign-off">Lorem Ipsum<br>is simply</div>

    <div class="footer-rule"></div>
    <div class="web-pill">www.marwicklaw.com</div>
  </div>
</body>
</html>
```